Business Card for Multi-Brand Sportswear Company

We are looking for a business card which represents our company and the multiple brands within it.

The company: Fen Athletics (LTD)
The brands: Fen, TavaPuni, ElmStretch, Grit and Rain

Employees using these cards would be representing Fen Athletics, rather than any of the individual brands. You will see a current design within the uploaded files, to give some inspiration. The actual text of the brands is not necessary, but the logos should be on there is some format.

Our creative minds on this are stretched, so we are looking for someone to make this their own, and show us what a good business card should look like.

We may like to get these printed with spot gloss, so keep that in mind with your designs.

www.fenathletics.co.uk

Industry/Entity Type

Business

Contact Information for Business Card

Leo Pemberton-Hale
Operations Manager
(+44) 1632 960 418
Leo@fenathletics.co.uk
www.fenathletics.co.uk

Font styles to use
Sans Serif
Other font styles liked:
• Eurostile

Colors
ffffff

Requirements
Nice to have
• Dark (black) background

```html
<!DOCTYPE html>
<html lang="en">
<head>
<meta charset="utf-8">
<title>Fen Athletics – Business Card</title>
<link href="https://fonts.googleapis.com/css2?family=Lato:wght@400;700&display=swap" rel="stylesheet">
<style>
  :root {
    --stage: #6b6b6b;
    --card-dark: #000000;
    --card-light: #ffffff;
    --card-light-shade: #e6e6e6;
    --accent-red: #e3161f;
    --tab-red: #b3121a;
    --text-light: #ffffff;
    --text-dark: #3a3a3a;
    --brand-purple: #5e4a6a;
    --brand-grey: #8a8a8a;
  }
  html, body {
    margin: 0;
    width: 1200px;
    height: 900px;
    overflow: hidden;
    background: var(--stage);
    font-family: 'Lato', sans-serif;
  }
  .stage { position: relative; width: 1200px; height: 900px; }

  .card {
    position: absolute;
    box-shadow: 0 2px 6px rgba(0,0,0,0.35);
  }
  .card-front {
    left: 265px; top: 200px; width: 310px; height: 502px;
    background: var(--card-dark);
    border-radius: 56px 0 56px 0;
    color: var(--text-light);
  }
  .card-back {
    left: 641px; top: 200px; width: 309px; height: 496px;
    background: radial-gradient(ellipse at 55% 50%, var(--card-light-shade) 0%, var(--card-light) 62%);
    border-radius: 0 56px 0 56px;
  }

  .wordmark {
    position: absolute;
    display: flex;
    align-items: center;
    gap: 8px;
    font-weight: 700;
    letter-spacing: 1px;
    white-space: nowrap;
  }
  .wordmark-mark { width: 12px; height: 12px; background: var(--accent-red); }
  .front-wordmark { left: 18px; top: 80px; font-size: 26px; color: var(--text-light); }
  .back-wordmark { left: 18px; top: 242px; font-size: 28px; color: var(--text-dark); }

  .holder-name {
    position: absolute; left: 17px; top: 250px;
    margin: 0; font-size: 19px; font-weight: 700;
    color: var(--accent-red); text-transform: uppercase; letter-spacing: 0.3px;
  }
  .holder-role {
    position: absolute; left: 17px; top: 274px;
    margin: 0; font-size: 14px; text-transform: uppercase; letter-spacing: 0.3px;
  }

  .contact-list {
    position: absolute; left: 0; top: 324px;
    margin: 0; padding: 0; list-style: none;
  }
  .contact-item {
    display: flex; align-items: center; height: 19.5px;
    font-size: 16px;
  }
  .contact-tab {
    width: 31px; height: 14px; margin-right: 6px;
    background: var(--tab-red);
    display: flex; align-items: center; justify-content: center;
  }
  .contact-tab svg { width: 10px; height: 10px; }

  .address {
    position: absolute; left: 17px; top: 408px;
    margin: 0; font-style: normal; font-size: 16px; line-height: 20px;
  }

  .brand-row {
    position: absolute; left: 22px; top: 386px; width: 276px;
    display: flex; justify-content: space-between; align-items: center;
    font-size: 11px; font-weight: 700; white-space: nowrap;
  }
  .brand-fen { color: var(--card-dark); }
  .brand-tavapuni { color: var(--accent-red); }
  .brand-elmstretch { color: var(--brand-purple); }
  .brand-gritrain { color: var(--brand-grey); }
</style>
</head>
<body>
<main class="stage">
  <section class="card card-front" aria-label="Business card front">
    <div class="wordmark front-wordmark"><span>FEN ATHLETICS</span><span class="wordmark-mark"></span></div>

    <h1 class="holder-name">Leo Pemberton-Hale</h1>
    <p class="holder-role">Managing Director</p>

    <ul class="contact-list">
      <li class="contact-item">
        <span class="contact-tab"><svg viewBox="0 0 10 10"><rect x="2.5" y="0.5" width="5" height="9" rx="1" fill="none" stroke="#fff" stroke-width="1"/><circle cx="5" cy="8" r="0.6" fill="#fff"/></svg></span>
        +44(0)1632 960418
      </li>
      <li class="contact-item">
        <span class="contact-tab"><svg viewBox="0 0 10 10"><rect x="0.5" y="2" width="9" height="6" fill="#fff"/><path d="M0.5 2 L5 5.5 L9.5 2" fill="none" stroke="#b3121a" stroke-width="0.9"/></svg></span>
        leo@fenathletics.co.uk
      </li>
      <li class="contact-item">
        <span class="contact-tab"><svg viewBox="0 0 10 10"><circle cx="5" cy="5" r="4.3" fill="#fff"/><path d="M2.5 3.5 Q4 2.5 4.5 4 Q3.5 5.5 5 6.5 L4.5 8.5 M6 2 Q7.5 3.5 8 5" fill="none" stroke="#b3121a" stroke-width="0.9"/></svg></span>
        www.fenathletics.co.uk
      </li>
    </ul>

    <address class="address">Marsh Lane,<br>Eldbury,Fenmore,FE7 3AH</address>
  </section>

  <section class="card card-back" aria-label="Business card back">
    <div class="wordmark back-wordmark"><span>FEN ATHLETICS</span><span class="wordmark-mark"></span></div>

    <div class="brand-row" aria-label="Group brands">
      <span class="brand-fen">Fen</span>
      <span class="brand-tavapuni">TavaPuni</span>
      <span class="brand-elmstretch">ElmStretch</span>
      <span class="brand-gritrain">Grit and Rain</span>
    </div>
  </section>
</main>
</body>
</html>
```